Interior Design for Every Day, Nora Whitfield Interior Design, LLC

We are looking for a website for an Interior Design Company targeted at higher income households. We prefer to work with clients that seek to amplify the architectural beauty of their interior space via interior design - while ensuring the space promotes easy living. For example: a kitchen should be lain out in an intuitive manner such that all utensils, cups and plates are easy to find. Living rooms should be arranged to promote conversation and/or watch TV, etc.... We have heavy reliance on the technical aspects of design (computer automated renderings). We like the look and feel of this website: https://www.brenthalvorsen.example/portfolioall

Target Market(s)

Upper HHI ($200,000+) in the Atlanta Metro Market. Customers are likely to be highly educated and from a variety of cultural backgrounds. Ages 35-60

Industry/Entity Type

Architecture

Font styles to use
Sans Serif

Colors

Designer to choose colors to be used in the design.

Requirements
Must have
• Landing Page, Page demonstrating how interior design fits into the architectural design process, About Us Page with contact info, Example Work Page and Tailored Client Page. Minimal work can be done on the About Us and example work pages. The tailored client page just needs a good layout (and easy uploads and download capability)
• Also to include:
• (1) The landing page should include a Design Philosophy Section and maybe a couple examples of our work and/or pictures you provide
• (2) The Design Process page should explain all steps of the architectural Design process and should explain where interior design/decorating fits into the Architectural process (see below attachments).
• (3) The Example work page should include areas for portfolio example uploads (to include 3 dimensional and 2 dimensional renderings, photos and videos).
• (4) Include a Password Protected, Secure Place where each individual client can store and retrieve documents and work product for their project (Should be a separate page). There should be sections (for each client) for:
• (a) there should be a client account creation requirement page that requires: FN, LN, Mobile, email, Work phone, Property address, City, Zip (for 3 properties), Spouse FN, Spouse LN, Child FN, LN (space for 5 children)
• (a) section: Legal & Invoices
• (b) section: Drawings & Renderings
• (c) section: Pin Ups (easy uploads of pictures from sites like snapboardia would be appreciated) - pin ups should be very easy for clients to put examples of what they like
• (5) Ability for admin to use personalized password and username to view, delete and edit client files (we utilize filecrate for document storage currently, and integration with filecrate would be a plus)
• (6) needs to be formatted and optimized for Mobile (iOs and android) viewing as well as Web
• (7) The site should be built with a hosting service contemplated. This service should be affordable (Less than $300 per annum)
• (8) most importantly the site should be minimalist with focus on user friendliness while being fashion forward
• (9) Website Color scheme should be White/Black/BlueGrey
• (10) The site must also include the ability to generate an invoice, based on client registration, electronically submit the invoice to the client via email (or print it), accept payment via coinvoy integration, and generate conformation email of payment to both client and admin (although coinvoy may already do this).
Nice to have
• Ability of example and client pages to be integrated with sites like snapbordia and filecrate. Ability to have some sort of section that self identifies the clients design style(s)...maybe a quiz or at lease a place where they can create a pinboard of images and colors they like (potentially by room)
Should not have
• Must look modern and be extremely quick/user friendly. Our clients are very busy.

```html
<!DOCTYPE html>
<html lang="en">
<head>
<meta charset="utf-8">
<title>Nora Whitfield Interior Design</title>
<link href="https://fonts.googleapis.com/css2?family=Lato:wght@400;700;900&family=Open+Sans:wght@400&display=swap" rel="stylesheet">
<style>
  :root {
    --page: #f7f7f7;
    --ink: #2e2e2e;
    --ink-soft: #5a5a5a;
    --accent: #3d4a58;
    --accent-light: #4a5b6d;
    --line: #9a9a9a;
    --frame: #ffffff;
  }
  * { margin: 0; padding: 0; box-sizing: border-box; }
  html, body { width: 1181px; height: 1200px; overflow: hidden; background: var(--page); }
  body { position: relative; font-family: "Lato", sans-serif; color: var(--ink); }

  .brand {
    position: absolute; left: 84px; top: 56px;
    display: flex; align-items: center; gap: 10px;
  }
  .brand-mark { width: 14px; height: 14px; background: var(--accent); }
  .brand-name { font-weight: 700; font-size: 15px; line-height: 18px; color: var(--ink); white-space: nowrap; }

  .phone { position: absolute; left: 924px; top: 16px; display: flex; align-items: center; gap: 16px; }
  .phone-icon { width: 32px; height: 32px; border: 1px solid #bdbdbd; border-radius: 50%; display: flex; align-items: center; justify-content: center; }
  .phone-number { font-size: 17px; letter-spacing: 1px; color: var(--ink-soft); }

  .main-nav { position: absolute; right: 97px; top: 72px; display: flex; align-items: center; gap: 27px; font-size: 15px; }
  .main-nav a { color: var(--ink); text-decoration: none; }
  .main-nav a.current { color: var(--accent-light); }

  .hero {
    position: absolute; left: 97px; top: 130px; width: 987px; height: 521px;
    background: var(--frame); border: 1px solid #e2e2e2; padding: 3px;
  }
  .hero-image {
    position: relative; width: 100%; height: 100%; overflow: hidden;
    background: linear-gradient(180deg, #dcdcdc 0%, #c9c9c7 45%, #a9aaa6 80%, #7d8078 100%);
  }
  .hero-corner { position: absolute; right: 0; bottom: 0; }

  .welcome { position: absolute; left: 0; top: 718px; width: 1181px; text-align: center; }
  .welcome h1 { font-size: 30px; font-weight: 400; letter-spacing: 0.3px; }
  .welcome h1 strong { font-weight: 900; }
  .welcome p {
    width: 740px; margin: 20px auto 0; font-family: "Open Sans", sans-serif;
    font-size: 12.6px; line-height: 28.7px; color: var(--ink-soft);
  }
  .button-about {
    display: inline-block; margin-top: 30px; width: 128px; height: 42px; line-height: 40px;
    border: 1px solid #8a8a8a; color: var(--accent); font-weight: 700; font-size: 14px;
    letter-spacing: 0.5px; text-decoration: none;
  }

  .divider { position: absolute; left: 97px; top: 1011px; width: 987px; height: 1px; background: var(--line); }

  .social { position: absolute; left: 0; top: 1074px; width: 1181px; display: flex; justify-content: center; gap: 22px; }
  .social a { display: flex; align-items: center; gap: 8px; color: var(--accent); text-decoration: none; font-size: 13px; }
  .social .dot { width: 40px; height: 40px; border: 1px solid #9a9a9a; border-radius: 50%; }

  .copyright {
    position: absolute; left: 0; top: 1137px; width: 1181px; text-align: center;
    font-family: "Open Sans", sans-serif; font-size: 11.8px; color: var(--ink-soft);
  }
</style>
</head>
<body>
  <header>
    <div class="brand">
      <span class="brand-mark"></span>
      <span class="brand-name">Nora Whitfield Interior Design</span>
    </div>

    <div class="phone">
      <span class="phone-icon">
        <svg width="12" height="12" viewBox="0 0 24 24" aria-hidden="true">
          <path fill="#3d4a58" d="M6.6 10.8a15.1 15.1 0 0 0 6.6 6.6l2.2-2.2a1 1 0 0 1 1-.25 11.4 11.4 0 0 0 3.6.57 1 1 0 0 1 1 1V20a1 1 0 0 1-1 1A17 17 0 0 1 3 4a1 1 0 0 1 1-1h3.5a1 1 0 0 1 1 1c0 1.250.2 2.450.57 3.57a1 1 0 0 1-.25 1z"/>
        </svg>
      </span>
      <span class="phone-number">404. 555. 0187</span>
    </div>

    <nav class="main-nav">
      <a class="current" href="#">HOME</a>
      <a href="#">PROCESS</a>
      <a href="#">ABOUT US</a>
      <a href="#">EXAMPLE WORKS</a>
      <a href="#">CLIENT CORNER</a>
      <a href="#">CONTACT US</a>
      <svg width="16" height="16" viewBox="0 0 24 24" aria-label="Search">
        <circle cx="10" cy="10" r="6.5" fill="none" stroke="#2e2e2e" stroke-width="3"/>
        <line x1="15" y1="15" x2="21" y2="21" stroke="#2e2e2e" stroke-width="3.4" stroke-linecap="round"/>
      </svg>
    </nav>
  </header>

  <section class="hero">
    <div class="hero-image" role="img" aria-label="Sketch-style rendering of a two-storey clapboard house front with a covered porch, dark front door, shuttered windows and shrubs">
      <svg class="hero-corner" width="162" height="189" viewBox="0 0 162 189" aria-hidden="true">
        <polygon points="162,0 162,189 0,189" fill="#3d4a58"/>
        <polygon points="162,59 162,189 51,189" fill="#4a5b6d"/>
      </svg>
    </div>
  </section>

  <section class="welcome">
    <h1><strong>WELCOME TO</strong> NORA WHITFIELD</h1>
    <p>Nam libero tempore, cum soluta nobis est eligendi optio cumque nihil impedit quo minus id quod maxime plac eat facere possimus, omnis voluptas assumenda est, omnis dolor repellendus. Temporibus autem quibusdam et aut officiis debitis aut rerum necessitatibus saepe eveniet ut et voluptates repudiandae sint et molestiae.</p>
    <a class="button-about" href="#">ABOUT US</a>
  </section>

  <div class="divider"></div>

  <footer>
    <div class="social">
      <a href="#"><span class="dot"></span>Facepage</a>
      <a href="#"><span class="dot"></span>Chirply</a>
      <a href="#"><span class="dot"></span>Instaframe</a>
      <a href="#"><span class="dot"></span>Snapboardia</a>
    </div>
    <p class="copyright">Copyrights © 2017,&nbsp; Nora Whitfield Interior Design. All Rights Reserved.</p>
  </footer>
</body>
</html>
```